Business Card Update, need to bring life to the card, two sided color

We need a new business card design, are moving and changing addresses and need a new look, we have the logos already attached but need a new style moving forward. Can incorporate the color of the logo (The Green) as well, maybe a solid back? We deal with safety products revolving around static electricity and safety lighting. Would like to keep same font in second logo as well.

Target Market(s)

Electrical Safety, Lighting

Contact Information for Business Card

Dale Fenwick
Vice President
Office: 770-555-4821
Cell: 770-555-3067
dale@tkfenwick.example
www.tkfenwick.example
4700 West Harbor Boulevard
Suite #150
Roswell, GA 30076

Font styles to use
Serif
Sans Serif

Requirements
Must have
• Since 1918
Nice to have
• Could use the 100 Year Logo for back of card, would like the back of card to be the same green as logo.
Should not have
• No black cards please.

```html
<!DOCTYPE html>
<html lang="en">
<head>
<meta charset="utf-8">
<title>T. K. Fenwick Business Card</title>
<link rel="stylesheet" href="https://fonts.googleapis.com/css2?family=Arimo:wght@700&family=Open+Sans:wght@400;600&display=swap">
<style>
  :root {
    --green: #00965a;
    --deep: #0c3b29;
    --deep-text: #0a2e20;
    --white: #ffffff;
    --stage: #eef3f0;
    --frame: #111111;
  }
  * { margin: 0; padding: 0; box-sizing: border-box; }
  html, body { width: 1200px; height: 1008px; overflow: hidden; background: var(--stage); }
  .canvas {
    position: relative; width: 1403px; height: 1178px;
    transform: scale(0.85531); transform-origin: 0 0;
    border: 3px solid var(--frame); background: var(--stage);
  }
  .card { position: absolute; overflow: hidden; }
  .card-front {
    left: 100px; top: 32px; width: 913px; height: 525px;
    border-radius: 52px; border: 1px solid #333; background: var(--white);
  }
  .front-bg { position: absolute; inset: 0; display: block; }
  .brand { position: absolute; font-family: "Arimo", Arial, sans-serif; font-weight: 700; }
  .brand-front { left: 155px; top: 40px; display: flex; align-items: center; gap: 18px; color: var(--green); }
  .brand-mark { width: 150px; height: 150px; border-radius: 50%; background: var(--green); flex: none; }
  .brand-name { font-size: 50px; line-height: 1; text-align: center; }
  .brand-name small { display: block; font-size: 23.5px; letter-spacing: 0.6px; margin-top: 6px; }
  .since {
    display: block; font-family: "Open Sans", Arial, sans-serif; font-weight: 600;
    font-size: 18px; letter-spacing: 5px; text-transform: uppercase; margin-top: 10px;
  }
  .person { position: absolute; left: 106px; top: 278px; font-family: "Arimo", Arial, sans-serif; font-weight: 700; }
  .person-name { color: var(--white); font-size: 36px; line-height: 42px; }
  .person-title { color: var(--deep-text); font-size: 34px; line-height: 44px; }
  .avatar {
    position: absolute; left: 401px; top: 254px; width: 128px; height: 128px;
    border-radius: 50%; background: var(--deep); border: 3px solid var(--white);
  }
  .contact { position: absolute; font-family: "Open Sans", Arial, sans-serif; color: var(--white); font-size: 20px; }
  .contact-row { display: flex; align-items: center; gap: 8px; height: 30px; white-space: nowrap; }
  .contact-row svg { width: 19px; height: 19px; flex: none; }
  .contact-row .label { color: #9fe0c2; }
  .address { left: 104px; top: 404px; line-height: 30px; }
  .address .indent { padding-left: 27px; white-space: nowrap; }
  .lines { left: 548px; top: 390px; }
  .card-back {
    left: 377px; top: 601px; width: 915px; height: 522px;
    border-radius: 56px; background: var(--green);
  }
  .back-mark {
    position: absolute; left: 342px; top: 22px; width: 230px; height: 230px;
    border-radius: 50%; background: var(--deep);
  }
  .brand-back { left: 0; right: 0; top: 285px; color: var(--deep-text); }
  .brand-back small { margin-top: 4px; }
  .brand-back .since { text-align: center; margin-top: 14px; }
  .back-url {
    position: absolute; left: 0; right: 0; top: 470px; text-align: center;
    font-family: "Open Sans", Arial, sans-serif; font-size: 30px; letter-spacing: 6px; color: var(--deep-text);
  }
</style>
</head>
<body>
<div class="canvas">
  <section class="card card-front">
    <svg class="front-bg" viewBox="0 0 913 525" width="913" height="525">
      <path d="M0 266H913V319H470V376H0Z" fill="var(--green)"/>
      <rect x="0" y="376" width="470" height="3" fill="var(--white)"/>
      <path d="M470 318H913V525H0V379H470Z" fill="var(--deep)"/>
    </svg>
    <div class="brand brand-front">
      <div class="brand-mark"></div>
      <div class="brand-name">T. K. Fenwick<small>Manufacturing Company, Inc.</small><span class="since">Since 1918</span></div>
    </div>
    <div class="person">
      <div class="person-name">Dale Fenwick</div>
      <div class="person-title">Vice President</div>
    </div>
    <div class="avatar" role="img" aria-label="Portrait photo placeholder"></div>
    <div class="contact address">
      <div class="contact-row">
        <svg viewBox="0 0 20 20"><path d="M10 2a6 6 0 0 0-6 6c0 4.5 6 10 6 10s6-5.5 6-10a6 6 0 0 0-6-6z" fill="none" stroke="var(--green)" stroke-width="1.8"/><circle cx="10" cy="8" r="2.2" fill="var(--green)"/></svg>
        <span>4700 West Harbor Boulevard</span>
      </div>
      <div class="indent">Suite #150</div>
      <div class="indent">Roswell, GA 30076</div>
    </div>
    <div class="contact lines">
      <div class="contact-row">
        <svg viewBox="0 0 20 20"><circle cx="10" cy="10" r="8.5" fill="none" stroke="var(--green)" stroke-width="1.6"/><path d="M7 5.5l1.6 2.3-1 1.2c.6 1.3 1.5 2.2 2.8 2.8l1.2-1 2.3 1.6-.8 1.8c-3.6-.3-6.7-3.4-7-7z" fill="var(--green)"/></svg>
        <span><span class="label">Office:</span> 770-555-4821</span>
      </div>
      <div class="contact-row">
        <svg viewBox="0 0 20 20"><rect x="5.5" y="2" width="9" height="16" rx="1.8" fill="none" stroke="var(--green)" stroke-width="1.6"/><circle cx="10" cy="15" r="1" fill="var(--green)"/></svg>
        <span><span class="label">Cell:</span> 770-555-3067</span>
      </div>
      <div class="contact-row">
        <svg viewBox="0 0 20 20"><circle cx="10" cy="10" r="8.5" fill="none" stroke="var(--green)" stroke-width="1.6"/><rect x="5.5" y="7" width="9" height="6.5" fill="none" stroke="var(--green)" stroke-width="1.4"/><path d="M5.5 7l4.5 3.5L14.5 7" fill="none" stroke="var(--green)" stroke-width="1.4"/></svg>
        <span>dale@tkfenwick.example</span>
      </div>
      <div class="contact-row">
        <svg viewBox="0 0 20 20"><g fill="none" stroke="var(--green)" stroke-width="1.4"><circle cx="10" cy="10" r="8.5"/><ellipse cx="10" cy="10" rx="3.8" ry="8.5"/><path d="M1.5 10h17M3 6h14M3 14h14"/></g></svg>
        <span>www.tkfenwick.example</span>
      </div>
    </div>
  </section>

  <section class="card card-back">
    <div class="back-mark"></div>
    <div class="brand brand-back">
      <div class="brand-name">T. K. Fenwick<small>Manufacturing Company, Inc.</small><span class="since">Since 1918</span></div>
    </div>
    <div class="back-url">www.tkfenwick.example</div>
  </section>
</div>
</body>
</html>
```